Corvel Capital LLC

Need Professional Business cards for New Investment Fund

Target Market(s)

High Quality investors

Industry/Entity Type

Financial

Contact Information for Business Card

Phone Number +1 555 284 6190
Name Lukas Varenko
Title Fund Manager
email lv@FundCorvel.com
Website www.FundCorvel.com

Colors

Designer to choose colors to be used in the design.

Requirements
Must have
• Must have our Logo and all of the above. Must be made so lettering and loge can be raised

```html
<!DOCTYPE html>
<html lang="en">
<head>
<meta charset="utf-8">
<title>Corvel Capital LLC – Business Card</title>
<link href="https://fonts.googleapis.com/css2?family=Roboto:wght@400;500;700&display=swap" rel="stylesheet">
<style>
  :root {
    --backdrop: #2a2a2a;
    --card: #1a1a1a;
    --accent: #86c01b;
    --text-light: #e4e4e4;
    --mark-dark: #3a3a3a;
    --mark-light: #eeeeee;
  }
  * { margin: 0; padding: 0; box-sizing: border-box; }
  html, body {
    width: 1200px; height: 1138px; overflow: hidden;
    background: var(--backdrop);
    font-family: 'Roboto', Arial, sans-serif;
  }
  .canvas { position: relative; width: 1200px; height: 1138px; }
  .card {
    position: absolute;
    width: 620px; height: 373px;
    background: var(--card);
    border-radius: 14px;
    overflow: hidden;
  }
  .card--front { left: 275px; top: 186px; }
  .card--back { left: 276px; top: 608px; }

  .wordmark {
    position: absolute;
    font-weight: 500;
    letter-spacing: 1px;
    line-height: 1;
    white-space: nowrap;
  }
  .card--front .wordmark {
    left: 0; right: 0; top: 142px;
    text-align: center;
    font-size: 84px;
    color: var(--mark-dark);
  }
  .card--back .wordmark {
    right: 33px; top: 262px;
    font-size: 58px;
    color: var(--mark-light);
  }

  .accent-tab {
    position: absolute; left: -36px; top: 44px;
    width: 48px; height: 76px;
    border-radius: 50%;
    background: var(--accent);
  }
  .holder { position: absolute; left: 34px; top: 55px; }
  .holder__name {
    font-size: 24px; font-weight: 700; color: var(--accent); line-height: 1.2;
  }
  .holder__title {
    font-size: 16px; color: var(--text-light); margin-top: 3px;
  }

  .contacts {
    position: absolute; left: 34px; top: 214px;
    list-style: none;
  }
  .contacts li {
    display: flex; align-items: center;
    height: 23.5px;
    font-size: 16px; color: var(--text-light);
  }
  .contacts svg { width: 16px; height: 14px; margin-right: 16px; fill: var(--accent); }
  .address {
    position: absolute; left: 34px; top: 292px;
    font-size: 16px; color: var(--text-light); line-height: 23.5px;
    font-style: normal;
  }
</style>
</head>
<body>
<div class="canvas">

  <section class="card card--front">
    <div class="wordmark">Corvel</div>
  </section>

  <section class="card card--back">
    <div class="accent-tab"></div>
    <div class="holder">
      <div class="holder__name">Lukas Varenko</div>
      <div class="holder__title">Fund Manager</div>
    </div>

    <ul class="contacts">
      <li>
        <svg viewBox="0 0 16 14" aria-hidden="true"><path d="M1 4c0-2 3-3 7-3s7 1 7 3v1h-3V4H4v1H1zM3 6h10l2 7H1z"/></svg>
        +1 555 284 6190
      </li>
      <li>
        <svg viewBox="0 0 16 14" aria-hidden="true"><path d="M1 2h14v10H1zM2 3l6 5 6-5v1L8 9 2 4z" fill-rule="evenodd"/></svg>
        lv@FundCorvel.com
      </li>
      <li>
        <svg viewBox="0 0 16 14" aria-hidden="true"><path d="M8 0a7 7 0 1 0 0 14A7 7 0 0 0 8 0zm0 1.2a5.8 5.8 0 1 1 0 11.6A5.8 5.8 0 0 1 8 1.2zM7.4 1h1.2v12H7.4zM1 6.4h14v1.2H1z"/></svg>
        www.FundCorvel.com
      </li>
    </ul>

    <address class="address">
      48 Alder Row<br>
      Eastfield, NJ, 08120
    </address>

    <div class="wordmark">Corvel</div>
  </section>

</div>
</body>
</html>
```